Now Leasing Banner

Looking for a banner that says the following information approx 4' x 30'

Now Leasing Maplebrook Terrace 925-318-6042

Target Market(s)

Drive by traffic

Industry/Entity Type

Residential property management

Requirements
Must have
• Clear and readable from a distance

```html
<!DOCTYPE html>
<html lang="en">
<head>
<meta charset="utf-8">
<title>Now Leasing Banner – Maplebrook Terrace</title>
<link rel="stylesheet" href="https://fonts.googleapis.com/css2?family=Montserrat:wght@700&family=Pinyon+Script&display=swap">
<style>
  :root {
    --page-bg: #ffffff;
    --brand-brown: #4a2e0f;
    --panel-cream: #e6e7df;
    --phone-green: #7f9155;
    --headline-white: #ffffff;
    --frame-grey: #c8c8c4;
    --sepia-dark: #8a6a43;
    --sepia-mid: #b39a76;
    --sepia-light: #e4ddcd;
  }
  * { margin: 0; padding: 0; box-sizing: border-box; }
  html, body {
    width: 1200px;
    height: 325px;
    overflow: hidden;
    background: var(--page-bg);
  }
  .canvas {
    position: relative;
    width: 1200px;
    height: 325px;
  }
  .banner {
    position: absolute;
    left: 41px;
    top: 87px;
    width: 1118px;
    height: 150px;
    display: flex;
    border: 1px solid var(--frame-grey);
    box-shadow: 0 2px 4px rgba(0, 0, 0, 0.18);
    background: var(--panel-cream);
  }
  .headline-panel {
    width: 391px;
    height: 100%;
    background: var(--brand-brown);
    padding: 11px 0 0 34px;
  }
  .headline {
    font-family: "Montserrat", sans-serif;
    font-weight: 700;
    color: var(--headline-white);
    font-size: 65px;
    line-height: 63px;
    letter-spacing: -0.5px;
    text-shadow: 0 1px 2px rgba(0, 0, 0, 0.35);
  }
  .details-panel {
    flex: 1;
    position: relative;
  }
  .property-name {
    position: absolute;
    left: 40px;
    top: 4px;
    font-family: "Pinyon Script", cursive;
    font-size: 58px;
    line-height: 80px;
    color: var(--brand-brown);
    white-space: nowrap;
  }
  .phone {
    position: absolute;
    left: 40px;
    top: 78px;
    font-family: "Montserrat", sans-serif;
    font-weight: 700;
    font-size: 57px;
    line-height: 60px;
    color: var(--phone-green);
    letter-spacing: -0.5px;
    white-space: nowrap;
  }
  .property-illustration {
    width: 255px;
    height: 100%;
    background: linear-gradient(100deg, var(--sepia-mid) 0%, var(--sepia-light) 45%, var(--sepia-mid) 75%, var(--sepia-dark) 100%);
  }
</style>
</head>
<body>
  <div class="canvas">
    <div class="banner">
      <div class="headline-panel">
        <h1 class="headline">NOW<br>LEASING</h1>
      </div>
      <div class="details-panel">
        <p class="property-name">Maplebrook Terrace</p>
        <p class="phone">925.318.6042</p>
      </div>
      <div class="property-illustration" role="img" aria-label="Sepia sketch of the apartment building framed by trees and a fence"></div>
    </div>
  </div>
</body>
</html>
```